Human Resource Consulting practice needs a business card design

We need a business card design (double sided colour) for our Human Resource (HR) consulting practice in regional New South Wales, australia. Our business name is Staff Compass. We support small and medium business across the Mid North Coast of New South Wales by providing them with outsourced HR support, services and products to help them achieve compliance with workplace legislation and across all areas of the employment lifecycle from recruitment to termination and everything in between. Our corporate colours are hot pink and black. The final design should communicate professionalism, trust, people focus.
I have attached the current (old) business card for your reference.

Target Market(s)

Business owners and high level managers

Industry/Entity Type

Business

Contact Information for Business Card

Name
Title
Phone no
Mobile no
Address
PO Box
email address
website

Colors
e34197

Requirements
Must have
• Tempate for changing business card personal details including Name, position title, mobile number, email address.
• Keep current logo and colours as per attached
• Logo must be presented in 2 colours or black only not white
Nice to have
• One side logo and graphic only other side logo and personal details
Should not have
• Should not be the same as the current version (attached) but a modern interpretation.
• Does not need a busy reverse side with our list of services as per current version. I feel this is too busy.
• No photos

```html
<!DOCTYPE html>
<html lang="en">
<head>
<meta charset="utf-8">
<title>Staff Compass – Business Card</title>
<link rel="stylesheet" href="https://fonts.googleapis.com/css2?family=Exo+2:wght@400;500;600;700&display=swap">
<style>
  :root {
    --pink: #e6268d;
    --charcoal: #3a3a3c;
    --paper: #ffffff;
    --backdrop: #ececec;
    --light-text: #f2f2f2;
  }
  * { margin: 0; padding: 0; box-sizing: border-box; }
  html, body {
    width: 1200px; height: 803px; overflow: hidden;
    background: var(--backdrop);
    font-family: "Exo 2", sans-serif;
  }
  .card {
    position: absolute;
    width: 540px; height: 309px;
    background: var(--paper);
    overflow: hidden;
    box-shadow: 0 2px 10px rgba(0,0,0,0.12);
  }
  .card--front { left: 40px; top: 247px; }
  .card--back  { left: 620px; top: 247px; }
  .card__shapes { position: absolute; inset: 0; }

  .wordmark {
    position: absolute;
    font-family: "Exo 2", sans-serif;
    font-weight: 700;
    color: var(--pink);
    white-space: nowrap;
    letter-spacing: 0.2px;
  }
  .card--front .wordmark { left: 100px; top: 132px; font-size: 38px; }
  .card--back .wordmark { left: 22px; top: 160px; font-size: 27px; }

  .front__web {
    position: absolute;
    right: 15px; top: 18px;
    writing-mode: vertical-rl;
    font-size: 11px; font-weight: 500;
    color: var(--paper);
    letter-spacing: 0.6px;
  }

  .person { position: absolute; left: 272px; top: 82px; color: var(--light-text); }
  .person__name { font-size: 20px; font-weight: 600; letter-spacing: 1.6px; text-transform: uppercase; }
  .person__title { font-size: 9px; font-weight: 500; letter-spacing: 1.2px; text-transform: uppercase; margin-top: 4px; }

  .contacts { position: absolute; left: 272px; top: 168px; list-style: none; color: var(--light-text); }
  .contacts__item { display: flex; align-items: flex-start; gap: 8px; font-size: 10.5px; line-height: 13px; margin-bottom: 8px; }
  .contacts__icon { width: 14px; height: 14px; flex: none; }
</style>
</head>
<body>

<section class="card card--front" aria-label="Card front">
  <svg class="card__shapes" viewBox="0 0 540 309" width="540" height="309" aria-hidden="true">
    <path d="M484 0 H540 V309 H478 V52 Q478 10 484 0 Z" fill="var(--pink)"/>
  </svg>
  <p class="wordmark">Staff Compass</p>
  <p class="front__web">www.staffcompass.net</p>
</section>

<section class="card card--back" aria-label="Card back">
  <svg class="card__shapes" viewBox="0 0 540 309" width="540" height="309" aria-hidden="true">
    <rect x="470" y="0" width="70" height="309" fill="var(--pink)"/>
    <path d="M245 0 H452 Q490 0 496 40 V309 H245 Z" fill="var(--charcoal)"/>
    <rect x="245" y="82" width="12" height="38" fill="var(--pink)"/>
  </svg>
  <p class="wordmark">Staff Compass</p>

  <div class="person">
    <p class="person__name">Dana Whitlow</p>
    <p class="person__title">General Manager</p>
  </div>

  <ul class="contacts">
    <li class="contacts__item">
      <svg class="contacts__icon" viewBox="0 0 14 14" aria-hidden="true"><circle cx="7" cy="7" r="6.2" fill="none" stroke="currentColor" stroke-width="1"/><path d="M4.6 3.8 L5.8 3.6 L6.4 5.2 L5.6 5.8 Q6.2 7.6 8 8.4 L8.6 7.6 L10.2 8.2 L10 9.4 Q7.6 10.4 5.2 7.8 Q3.8 5.8 4.6 3.8 Z" fill="currentColor"/></svg>
      <span>02 6581 4270</span>
    </li>
    <li class="contacts__item">
      <svg class="contacts__icon" viewBox="0 0 14 14" aria-hidden="true"><circle cx="7" cy="7" r="6.2" fill="none" stroke="currentColor" stroke-width="1"/><rect x="5" y="3.4" width="4" height="7.2" rx="0.7" fill="none" stroke="currentColor" stroke-width="0.9"/><circle cx="7" cy="9.4" r="0.5" fill="currentColor"/></svg>
      <span>0418 552 093</span>
    </li>
    <li class="contacts__item">
      <svg class="contacts__icon" viewBox="0 0 14 14" aria-hidden="true"><circle cx="7" cy="7" r="6.2" fill="none" stroke="currentColor" stroke-width="1"/><rect x="3.8" y="4.8" width="6.4" height="4.4" fill="currentColor"/><path d="M3.8 4.8 L7 7.4 L10.2 4.8" fill="none" stroke="var(--charcoal)" stroke-width="0.8"/></svg>
      <span>dana@staffcompass.net</span>
    </li>
    <li class="contacts__item">
      <svg class="contacts__icon" viewBox="0 0 14 14" aria-hidden="true"><circle cx="7" cy="7" r="6.2" fill="none" stroke="currentColor" stroke-width="1"/><circle cx="7" cy="7" r="3.6" fill="none" stroke="currentColor" stroke-width="0.8"/><path d="M3.4 7 H10.6 M7 3.4 V10.6 M7 3.4 Q4.8 7 7 10.6 M7 3.4 Q9.2 7 7 10.6" fill="none" stroke="currentColor" stroke-width="0.6"/></svg>
      <span>www.staffcompass.net</span>
    </li>
    <li class="contacts__item">
      <svg class="contacts__icon" viewBox="0 0 14 14" aria-hidden="true"><circle cx="7" cy="7" r="6.2" fill="none" stroke="currentColor" stroke-width="1"/><path d="M7 10.8 Q4.4 7.6 4.4 6 A2.6 2.6 0 0 1 9.6 6 Q9.6 7.6 7 10.8 Z" fill="currentColor"/><circle cx="7" cy="6" r="0.9" fill="var(--charcoal)"/></svg>
      <span>27 Tallow Lane,<br>Level 2 Suite B.</span>
    </li>
  </ul>
</section>

</body>
</html>
```